Upmarket Dessert Lounge needs a Business Card Design

We are an upmarket dessert lounge needing a business card to match our image.

We want something that is simple yet beautiful, feminine, classy, sophisticated and elegant. We want it to stand out and don't mind if it is bold.

The design should include our logo and colours of red or maroon with gold highlights. We don't mind if black is used.

Marlow & Quince

Target Market(s)

For those who like to indulge or treat themselves and give in to their temptations on good quality desserts.

Industry/Entity Type

Business

Requirements
Must have
• Must include our logo and our name

Marlow & Quince

M & Q

```html
<!DOCTYPE html>
<html lang="en">
<head>
<meta charset="utf-8">
<title>Marlow &amp; Quince — Business Card</title>
<link href="https://fonts.googleapis.com/css2?family=Lato:wght@300;400;700&family=Pinyon+Script&display=swap" rel="stylesheet">
<style>
  :root {
    --maroon: #7a1517;
    --gold: #f8cf8f;
    --cream-gold: #f5d09a;
    --white: #ffffff;
    --page: #ffffff;
  }
  html, body {
    margin: 0;
    padding: 0;
    width: 900px;
    height: 1200px;
    overflow: hidden;
    background: var(--page);
  }
  .canvas {
    position: relative;
    width: 900px;
    height: 1200px;
  }
  .card {
    position: absolute;
    left: 84px;
    top: 60px;
    width: 721px;
    height: 1075px;
    background: var(--maroon);
    overflow: hidden;
  }
  .card__cloud {
    position: absolute;
    inset: 0;
    width: 721px;
    height: 1075px;
  }
  .card__cloud-shape {
    fill: var(--white);
    stroke: var(--gold);
    stroke-width: 13;
    stroke-linejoin: round;
  }
  .card__text {
    position: absolute;
    left: 0;
    width: 706px;
    margin: 0;
    text-align: center;
    font-family: "Lato", sans-serif;
  }
  .brand-mark {
    top: 204px;
    width: 684px;
    font-size: 56px;
    font-weight: 400;
    letter-spacing: 2px;
    line-height: 64px;
    color: var(--maroon);
  }
  .tagline {
    top: 345px;
    width: 718px;
    font-family: "Pinyon Script", cursive;
    font-size: 70px;
    line-height: 90px;
    font-weight: 400;
    color: var(--maroon);
  }
  .contacts {
    top: 482px;
    font-size: 29px;
    line-height: 40px;
    font-weight: 300;
    color: var(--maroon);
  }
  .contacts__name {
    font-weight: 700;
  }
  .address {
    top: 890px;
    font-size: 28px;
    line-height: 40px;
    font-weight: 300;
    color: var(--cream-gold);
  }
</style>
</head>
<body>
<main class="canvas">
  <section class="card" aria-label="Marlow &amp; Quince business card">
    <svg class="card__cloud" viewBox="84 60 721 1075" aria-hidden="true">
      <path class="card__cloud-shape" d="
        M 70 292
        C 105 274 132 263 158 256
        C 150 200 190 165 240 165
        C 268 132 300 124 325 130
        C 350 100 395 72 430 52
        L 600 52
        C 620 70 640 80 660 82
        C 700 70 760 72 815 80
        L 815 545
        C 790 570 760 592 728 620
        C 735 670 712 710 665 728
        C 660 770 620 790 580 785
        C 560 805 520 812 472 805
        C 440 838 390 855 320 850
        C 280 866 230 862 195 855
        C 150 848 110 845 70 850
        Z"/>
    </svg>

    <p class="card__text brand-mark">M &amp; Q</p>

    <h1 class="card__text tagline">Dessert Specialists</h1>

    <p class="card__text contacts">
      <span class="contacts__name">Marlow</span> 04321 77810<br>
      <span class="contacts__name">Quince</span> 04321 55926
    </p>

    <p class="card__text address">
      street name, district<br>
      Harbourton, Westvale Coast<br>
      Marlow-Quince.com
    </p>
  </section>
</main>
</body>
</html>
```